Folder and brochures for food service software solution

We offer integrated software solutions for independent and chain food service businesses. Such businesses would include fine dining restaurants, fast food outlets, home delivery, takeaways, cafeterias, event catering venues, institutional catering companies, hotels with restaurants / bars, etc. Our software is configured for the needs of each type of business and spans both guest facing and back office functions.

The core benefits our solution offers is that it is -
1. integrated to cater to all the needs of the food service business, both independent and chain, across most (not all, we do not do anything for labor management) functions.
2. functionally powerful and compare well with the best available internationally.
3. Developed using the latest in software technology ... for example, our EPOS software for Android devices.

The market is a mature market with many competitors. A few very well established with huge track record. We have a track record internationally but are new to the UK market. This brochure is targeted at the UK market. The target market is jaded with the number of options available. We will focus on fine dining outlets in the hope that our Android based EPOS will excite them. We will focus on events & catering because the competition in the segment is relatively thin. We will go after the institutional catering market because we offer strong cost control features. But we want to mention how we service all sub-segments of the food & beverage service business to convey the versatility of our solution and for the other businesses that we may be able to attract.

We are hoping that the brochure will stand-out from the crowd and will compel the market to browse through what we do.

Some key competitors in the UK include -
http://www.venbrook.co.uk/
http://www.q-til.co.uk/
http://www.harromax.co.uk/
http://dunvey.co.uk/

We have a company and product logo (both attached). Of these, we are open to dropping or redesgning the product logo. We have also developed a web site (see kbuk.tarvensystems.example). The brochure design need not conform to the web site, if (and only if) you can come up with a really attention design (we could consider redesign of the web site).

The content of the brochure will largely conform to the content at the web site. The content at the web site is structured by solutions for independent outlets (centered around the EPOS) and solutions for chains. It also mentions 18 products. This is too much for a print brochure. So, we propose the following structure -

1. a folder that also carries a brief about our company with facility to add inserts.
2. one brochure that describes the solutions offered, the market segments they apply to and the benefits of the solution for each segment.
3. A summary / list of the products that are used to configure the solution.

We will add product specific flyers to the folder by color laser printing these. This will provide us the flexibility to add only the few product sheets that are of relevance to each prospect and will allow us to update frequently. For this we will require a template so that all product sheets look similar ... possibly with a color theme separating the products for each outlet from those for the chain of outlets.

We can only provide low-res images. You will have to touch up screens to improve resolution of images to make them print-ready. You are free to propose purchase of reasonably priced general stock-shots subject to prior approval from us. We will pay for these images.
Updates

At least one of you have requested that we -

1. identify a key message and

2. compact the contents of the brochure 

To do so, we have had to take an alternative approach and revise the content completely. Please check back and see the latest uploads, both Marlo - Approach 2 and Marlo - Salient Features.

We hope this helps you in your design effort.                     

Reason: We understand that we are requesting this design through a holiday season. We are extending the deadline by a few days. If this also does not work for some of you, please let us know a realistic date by which you are able to provide us options. We will consider, even though we are on a tight time line.

Reason: Some of you are still working on final layouts At least one of you is waiting for us to provide you modified content to fit the design. The extra days are intended to allow you to provide a complete and final design.

Earlier, we had posted an update and new content. This was in response to the community's request to reduce content. Did you note that? It seems not. So, we have now removed older content and only retained the revised content as per the last update. Please verify that the design you propose is as per the latest content. In the process, we may have removed some images also. Need them? Let me know and I will re-post.

Reason: Further extension, open only to those that have previously submitted designs and need the extra time to finalize the design based on feedback from us.

Target Market(s)

Upper mid market fine dining restaurants, likely with home delivery / takeaway options.
Small food service chains (3 to 10 outlets).
Venues with catering facilities.
Cafeterias.
Bulk food suppliers / institutional caterers.
Food service business with a central kitchen / commissary and multiple service locations.
membership clubs with food service.

Industry/Entity Type

Software

Font styles to use
Sans Serif

Requirements
Must have
• A distinctive attention grabbing design.

The structure of -
1. a folder with facility for inserts.
2. two brochures.
3. template for product specific write-ups.
Nice to have
• Info-graphics to represent an integrated solution. Another to demonstrate versatility across types of F&B business.

A design that relates the solution to the UK ... either in terms of colors or visuals.

```html
<!DOCTYPE html>
<html lang="en">
<head>
<meta charset="utf-8">
<title>Marlo – Innovation, Technology, Minimal Risk</title>
<link href="https://fonts.googleapis.com/css2?family=Titillium+Web:wght@300;400;700&display=swap" rel="stylesheet">
<style>
  :root {
    --brand-red: #d7182a;
    --brand-red-dark: #a31c27;
    --heading-red: #9e1b25;
    --text-grey: #4a4a4a;
    --ring-grey: #e4e4e4;
    --page-top: #ffffff;
    --page-bottom: #e9e9ea;
    --photo-steel: #b9c3c8;
    --photo-warm: #7d6a55;
  }
  * { margin: 0; padding: 0; box-sizing: border-box; }
  html, body { width: 841px; height: 1200px; overflow: hidden; }
  body {
    font-family: "Titillium Web", sans-serif;
    background: linear-gradient(180deg, var(--page-top) 35%, var(--page-bottom) 100%);
    position: relative;
    color: var(--text-grey);
  }
  .hero { position: absolute; top: 0; left: 0; width: 841px; height: 390px; }
  .section-title {
    position: absolute;
    left: 49px;
    font-size: 27px;
    font-weight: 700;
    color: var(--heading-red);
    letter-spacing: -0.2px;
  }
  .badge { position: absolute; left: 50px; width: 146px; height: 160px; }
  .section-body {
    position: absolute;
    left: 234px;
    width: 577px;
    font-size: 13.6px;
    font-weight: 300;
    line-height: 20px;
    text-align: justify;
  }
  .section-body p { margin: 0; }
  .section-body .bullet::before { content: "\25AA"; margin-right: 5px; }
</style>
</head>
<body>

<svg class="hero" viewBox="0 0 841 390" aria-hidden="false">
  <defs>
    <linearGradient id="kitchenTone" x1="0" y1="0" x2="1" y2="0.3">
      <stop offset="0" stop-color="#cfe0e6"/>
      <stop offset="0.35" stop-color="#8f8f86"/>
      <stop offset="0.6" stop-color="var(--photo-warm)"/>
      <stop offset="1" stop-color="var(--photo-steel)"/>
    </linearGradient>
    <linearGradient id="bandRed" x1="0" y1="0" x2="1" y2="0">
      <stop offset="0" stop-color="var(--brand-red-dark)"/>
      <stop offset="1" stop-color="var(--brand-red)"/>
    </linearGradient>
  </defs>
  <polygon points="0,0 841,0 841,240 0,345" fill="url(#kitchenTone)" role="img" aria-label="Chefs cooking at the stoves of a stainless steel commercial kitchen"/>
  <polygon points="0,345 841,240 841,272 0,380" fill="url(#bandRed)"/>
</svg>

<h2 class="section-title" style="top:410px;">Superior Innovate at will</h2>
<svg class="badge" style="top:452px;" viewBox="0 0 146 160">
  <ellipse cx="73" cy="150" rx="50" ry="6" fill="#000" opacity="0.12"/>
  <circle cx="73" cy="72" r="70" fill="var(--ring-grey)"/>
  <circle cx="73" cy="72" r="64" fill="#fff"/>
  <circle cx="73" cy="72" r="55" fill="var(--brand-red)"/>
  <g fill="none" stroke="#fff" stroke-width="4">
    <ellipse cx="73" cy="72" rx="36" ry="13"/>
    <ellipse cx="73" cy="72" rx="36" ry="13" transform="rotate(60 73 72)"/>
    <ellipse cx="73" cy="72" rx="36" ry="13" transform="rotate(-60 73 72)"/>
  </g>
  <circle cx="73" cy="72" r="6" fill="#fff"/>
</svg>
<div class="section-body" style="top:478px;">
  <p>To be competitive, you need to innovate in terms of food, ambience, processes and business strategies. You will find Marlo and our software development team responsive to your evolving needs. Chances are that we will deliver you features that others will not or cannot. We can deliver custom features and applications at rates that are most competitive. We have a track record of doing so.</p>
</div>

<h2 class="section-title" style="top:636px;">Exploit the latest in technology</h2>
<svg class="badge" style="top:708px;" viewBox="0 0 146 160">
  <ellipse cx="73" cy="150" rx="50" ry="6" fill="#000" opacity="0.12"/>
  <circle cx="73" cy="72" r="70" fill="var(--ring-grey)"/>
  <circle cx="73" cy="72" r="64" fill="#fff"/>
  <circle cx="73" cy="72" r="55" fill="var(--brand-red)"/>
  <g fill="none" stroke="#fff" stroke-width="8" stroke-linecap="round">
    <path d="M35 60 A52 52 0 0 1 111 60"/>
    <path d="M47 73 A36 36 0 0 1 99 73"/>
    <path d="M59 86 A19 19 0 0 1 87 86"/>
  </g>
  <circle cx="73" cy="99" r="7" fill="#fff"/>
</svg>
<div class="section-body" style="top:683px;">
  <p class="bullet">Want to benefit from mobile point-of-sale technology? In food service or in business reporting? We will readily deliver you software for mobility.</p>
  <p class="bullet">Will you be able to drive more business by offering instant loyalty redemption at your chain outlets. We can deliver you a central loyalty accounting system to do so.</p>
  <p class="bullet">Do you wish to integrate with reservation &amp; order taking portals or with social media applications or with electronic payment processors? Tell us who and what you wish to interface with.</p>
  <p class="bullet">Do you want to exploit web based technology to establish a single back office for your chain of outlets? We offer software for it.</p>
  <p>Tarven Systems has a 15 year record of staying at the leading edge of software technology, internationally.</p>
</div>

<h2 class="section-title" style="top:881px;">Minimal risk</h2>
<svg class="badge" style="top:970px;" viewBox="0 0 146 160">
  <ellipse cx="73" cy="150" rx="50" ry="6" fill="#000" opacity="0.12"/>
  <circle cx="73" cy="72" r="70" fill="var(--ring-grey)"/>
  <circle cx="73" cy="72" r="64" fill="#fff"/>
  <circle cx="73" cy="72" r="55" fill="var(--brand-red)"/>
  <g fill="#fff">
    <rect x="42" y="82" width="12" height="24"/>
    <rect x="58" y="74" width="12" height="32"/>
    <rect x="74" y="80" width="12" height="26"/>
    <rect x="90" y="64" width="12" height="42"/>
  </g>
  <polyline points="40,74 60,54 78,66 102,42" fill="none" stroke="#fff" stroke-width="6" stroke-linejoin="round"/>
  <polygon points="92,36 110,34 108,52" fill="#fff"/>
</svg>
<div class="section-body" style="top:955px;">
  <p class="bullet">Want to benefit from mobile point-of-sale technology? In food service or in business reporting? We will readily deliver you software for mobility.</p>
  <p class="bullet">Will you be able to drive more business by offering instant loyalty redemption at your chain outlets. We can deliver you a central loyalty accounting system to do so.</p>
  <p class="bullet">Do you wish to integrate with reservation &amp; order taking portals or with social media applications or with electronic payment processors? Tell us who and what you wish to interface with.</p>
  <p class="bullet">Do you want to exploit web based technology to establish a single back office for your chain of outlets? We offer software for it.</p>
  <p>Tarven Systems has a 15 year record of staying at the leading edge of software technology, internationally.</p>
</div>

</body>
</html>
```